New profile page for existing party website

For the party website 'Partyvenz' we need a new design for the user profile page.

The page should show
* a profile picture
* basic information like name, age and city
* music styles he/she likes
* links to their Chatterbook profile and website
* a bio (HTML content)
* events they plan to go to
* past events
* pictures

Challenge is that some users may have little information (just their name) while others have a huge description, lots of foto's, events, etc.

Please visit http://www.partyvenz.example and http://www.partyvenz.example/users/bertil

Target Market(s)

Men and women between 18 and 35

Industry/Entity Type

Night Club

Number of Pages Required

2 page

Font styles to use
Other font styles liked:
• Roboto

Requirements
Must have
• Please design how the page looks with a fully filled out profile and with an empty profile.
• It should fit well with the existing website.
• Include designs for both for small screens (mobile) and large screens (tablet, desktop).
Nice to have
• UX design on how to collapse or paginate sections.
• Interactive effects would be a bonus.
Should not have
• The page should not have subnavigation like menus or tabs.

```html
<!DOCTYPE html>
<html lang="en">
<head>
<meta charset="utf-8">
<title>Partyvenz – My Profile</title>
<link rel="stylesheet" href="https://fonts.googleapis.com/css2?family=Roboto+Condensed:wght@400;700&family=Raleway:wght@400;700&family=Roboto:wght@400;500&display=swap">
<style>
  :root {
    --bg-page: #2b2b2b;
    --bg-header: #000000;
    --profile: #d99a00;
    --profile-tab: #ad7d00;
    --profile-frame: #a57800;
    --resume: #d66a18;
    --resume-tab: #953d05;
    --text-light: #ffffff;
    --text-soft: #fdf1dc;
    --button-border: #b98500;
  }
  * { box-sizing: border-box; margin: 0; padding: 0; }
  html, body { width: 1200px; height: 2490px; overflow: hidden; }
  body { background: var(--bg-page); font-family: "Raleway", sans-serif; color: var(--text-light); position: relative; }

  .site-header { position: absolute; left: 0; top: 0; width: 1200px; height: 156px; background: var(--bg-header); }
  .brand { position: absolute; left: 22px; top: 38px; font-family: "Roboto Condensed", sans-serif; font-size: 72px; font-weight: 400; color: var(--text-light); line-height: 80px; }
  .menu-toggle { position: absolute; left: 1048px; top: 36px; width: 106px; height: 80px; border: 2px solid #555; border-radius: 8px; background: #000; }
  .menu-toggle span { position: absolute; left: 28px; width: 50px; height: 6px; background: #fff; border-radius: 2px; }

  .panel { position: absolute; left: 42px; width: 1110px; }
  .panel-tab { position: absolute; left: 0; top: 0; height: 107px; display: flex; gap: 8px; }
  .tab-icon { width: 105px; height: 107px; display: flex; align-items: center; justify-content: center; }
  .tab-label { height: 107px; padding: 0 72px; display: flex; align-items: center; font-family: "Roboto Condensed", sans-serif; font-size: 44px; color: var(--text-light); }

  .profile { top: 202px; height: 1432px; background: var(--profile); }
  .profile .tab-icon, .profile .tab-label { background: var(--profile-tab); }
  .profile-photo { position: absolute; left: 305px; top: 183px; width: 501px; height: 625px; border: 15px solid var(--profile-frame); background: linear-gradient(160deg, #8a5a2c 0%, #5b3a22 45%, #a9793d 100%); }
  .profile-name { position: absolute; left: 0; top: 842px; width: 100%; text-align: center; font-family: "Roboto Condensed", sans-serif; font-size: 56px; font-weight: 400; }
  .profile-facts { position: absolute; left: 0; top: 945px; width: 100%; text-align: center; font-size: 36px; line-height: 57px; color: var(--text-soft); }
  .profile-facts b { font-weight: 700; color: var(--text-light); }
  .profile-links { position: absolute; left: 0; top: 1136px; width: 100%; display: flex; justify-content: center; gap: 18px; }
  .profile-links svg { width: 42px; height: 42px; }
  .manage-button { position: absolute; left: 408px; top: 1254px; width: 297px; height: 99px; border: 3px solid var(--button-border); border-radius: 6px; background: #c98d00; font-family: "Roboto", sans-serif; font-weight: 500; font-size: 32px; color: var(--text-light); display: flex; align-items: center; justify-content: center; }

  .resume { top: 1701px; height: 789px; background: var(--resume); }
  .resume .tab-icon, .resume .tab-label { background: var(--resume-tab); }
  .resume-body { position: absolute; left: 67px; top: 175px; right: 60px; }
  .resume-company { font-family: "Roboto Condensed", sans-serif; font-size: 54px; font-weight: 400; line-height: 64px; }
  .resume-line { margin-top: 26px; font-size: 36px; line-height: 46px; color: var(--text-soft); }
  .resume-line .label { font-family: "Roboto Condensed", sans-serif; font-size: 42px; color: var(--text-light); }
</style>
</head>
<body>
  <header class="site-header">
    <div class="brand">Partyvenz</div>
    <div class="menu-toggle" aria-label="Menu">
      <span style="top:24px"></span><span style="top:37px"></span><span style="top:50px"></span>
    </div>
  </header>

  <section class="panel profile">
    <div class="panel-tab">
      <div class="tab-icon">
        <svg width="46" height="46" viewBox="0 0 24 24" fill="#fff"><circle cx="12" cy="7" r="5"/><path d="M2 23c0-6 4-9 10-9s10 3 10 9z"/></svg>
      </div>
      <div class="tab-label">My Profile</div>
    </div>
    <div class="profile-photo" role="img" aria-label="Profile photo of the user"></div>
    <h1 class="profile-name">Bertil Marsh</h1>
    <p class="profile-facts"><b>Age</b> - 34<br><b>City</b> - Amsterdam,<br><b>Music</b> - Latin / Salsa</p>
    <div class="profile-links">
      <svg viewBox="0 0 24 24" aria-label="Chatterbook"><rect x="2" y="2" width="20" height="20" rx="4" fill="#fff"/></svg>
      <svg viewBox="0 0 24 24" aria-label="Video channel"><rect x="2" y="2" width="20" height="20" rx="4" fill="#fff"/></svg>
      <svg viewBox="0 0 24 24" aria-label="Website"><circle cx="12" cy="12" r="10" fill="#fff"/></svg>
      <svg viewBox="0 0 24 24" aria-label="Email"><rect x="1" y="4" width="22" height="16" rx="2" fill="#fff"/><path d="M2 6l10 7 10-7" fill="none" stroke="#d99a00" stroke-width="2"/></svg>
    </div>
    <div class="manage-button">Manage</div>
  </section>

  <section class="panel resume">
    <div class="panel-tab">
      <div class="tab-icon">
        <svg width="48" height="48" viewBox="0 0 24 24" fill="none" stroke="#fff" stroke-width="2.4"><path d="M12 4H5a2 2 0 0 0-2 2v13a2 2 0 0 0 2 2h13a2 2 0 0 0 2-2v-7"/><path d="M18 2.5l3.5 3.5L12 15.5H8.5V12z" fill="#fff" stroke="none"/></svg>
      </div>
      <div class="tab-label">Resume</div>
    </div>
    <div class="resume-body">
      <h2 class="resume-company">Lumenhoek Photography</h2>
      <p class="resume-line"><span class="label">Function :</span> Head promotions, photograper, communica-tion, marketing, and sales.</p>
      <p class="resume-line"><span class="label">Active since :</span> 2006</p>
    </div>
  </section>
</body>
</html>
```